Business card for Luxury Portable Restroom Trailer company

We are a Luxury Portable Restroom Trailer Company Called FALCRIDGE HIRES. Based in Orange County California. We provide portable restroom trailers for events, such as, Weddings, Concerts, Charity events, Sporting events, Tournaments, Corporate events, ect. We rent and Sell the Luxury restrooms. Our colors are white, grey, and Orange. As you will see in the logo we uploaded.
There are 2 people in the company so the names and titles will change for the 3 people but card will remain the same. Here is the information for each Person: Dwight Penner CFO 555 318-0476
next Person: Leon Marchetti VP 555 318-0476
Next Person: Owen Marchetti CEO 555 318-0476
Information to include on the card: Luxury Restroom Trailers Rental and Sales. Weddings, Concerts, Charity, Sporting and Corp. Events.

```html
<!DOCTYPE html>
<html lang="en">
<head>
<meta charset="utf-8">
<title>Falcridge Hires – Business Card</title>
<link rel="stylesheet" href="https://fonts.googleapis.com/css2?family=Arimo:wght@400;700&display=swap">
<style>
  :root {
    --page-bg: #e6e6e4;
    --card-white: #ffffff;
    --card-fade: #ececec;
    --card-dark: #48484b;
    --card-dark-deep: #3d3d40;
    --brand-orange: #ee5a16;
    --ink-grey: #4a4a4c;
    --text-dark: #3a3a3a;
  }
  * { box-sizing: border-box; margin: 0; padding: 0; }
  html, body { width: 1200px; height: 900px; overflow: hidden; }
  body {
    background: var(--page-bg);
    font-family: "Arimo", Arial, sans-serif;
    display: flex;
    flex-direction: column;
    align-items: center;
    justify-content: center;
    gap: 40px;
  }
  .card {
    width: 700px;
    height: 400px;
    border-radius: 34px;
    position: relative;
    overflow: hidden;
    box-shadow: 0 8px 22px rgba(0,0,0,0.18);
  }

  /* Back side */
  .card-back {
    background: var(--card-dark);
  }
  .card-back .pattern-area {
    position: absolute;
    inset: 0;
    background: radial-gradient(ellipse at 60% 40%, var(--card-dark) 0%, var(--card-dark-deep) 100%);
  }
  .card-back .back-brand {
    position: absolute;
    right: 70px;
    top: 170px;
    display: flex;
    align-items: center;
    gap: 12px;
    font-weight: 700;
    font-size: 22px;
    letter-spacing: 1px;
    color: var(--brand-orange);
  }
  .brand-circle {
    width: 22px; height: 22px;
    border-radius: 50%;
    border: 3px solid var(--brand-orange);
  }

  /* Front side */
  .card-front {
    background: linear-gradient(200deg, var(--card-white) 0%, var(--card-fade) 45%, var(--card-white) 100%);
  }
  .contact {
    position: absolute;
    left: 44px;
    top: 96px;
  }
  .person-name {
    font-weight: 700;
    font-size: 21px;
    letter-spacing: 0.5px;
    color: var(--brand-orange);
    text-transform: uppercase;
  }
  .person-role {
    margin-top: 6px;
    font-size: 17px;
    color: var(--text-dark);
  }
  .person-role .label { color: var(--brand-orange); }
  .services {
    position: absolute;
    left: 44px;
    top: 176px;
  }
  .services-title {
    font-weight: 700;
    font-size: 21px;
    color: var(--brand-orange);
    text-transform: uppercase;
  }
  .services-tagline {
    margin-top: 4px;
    font-size: 16px;
    color: var(--text-dark);
  }
  .service-list {
    list-style: none;
    margin-top: 8px;
    margin-left: 4px;
  }
  .service-list li {
    display: flex;
    align-items: center;
    gap: 10px;
    font-size: 16px;
    line-height: 25px;
    color: var(--text-dark);
  }
  .service-list li::before {
    content: "";
    width: 9px; height: 9px;
    border-radius: 50%;
    background: var(--brand-orange);
  }
  .front-brand {
    position: absolute;
    right: 46px;
    top: 238px;
    font-weight: 700;
    font-size: 38px;
    letter-spacing: 1px;
    color: var(--ink-grey);
  }
</style>
</head>
<body>
  <section class="card card-back" aria-label="Card back">
    <div class="pattern-area" role="img" aria-label="Tone-on-tone repeating brand mark pattern on dark grey"></div>
    <div class="back-brand"><span class="brand-circle"></span>FALCRIDGE HIRES</div>
  </section>

  <section class="card card-front" aria-label="Card front">
    <div class="contact">
      <p class="person-name">Dwight Penner</p>
      <p class="person-role">CFO | <span class="label">M.</span> 555 318-0476</p>
    </div>
    <div class="services">
      <p class="services-title">Our Services</p>
      <p class="services-tagline">Luxury Restroom Trailers Rental and Sales</p>
      <ul class="service-list">
        <li>Weddings</li>
        <li>Concerts</li>
        <li>Charity</li>
        <li>Sporting and Corp</li>
        <li>Events</li>
      </ul>
    </div>
    <p class="front-brand">FALCRIDGE HIRES</p>
  </section>
</body>
</html>
```